Business Card Design For Office Furniture Clearance Company

Kestrel Office Clearance - our company name pretty much explains what we do, we clear offices for high end clients, mainly plc's and large international companies.

We require a nice looking business card that displays professionalism but without being too serious.

It would be nice to see just a little more than a conventional boring business card, make sure you add some flare.

Industry/Entity Type

Office Furniture

Contact Information for Business Card

CARD 1

Mark Holloway
Director
mark@kestrelofficeclearance.co.uk
m: 07700 153928

t: 01632 960418
www.kestrelofficeclearance.co.uk

Kestrel Office Clearance
Unit K4 B
2-8 Fenwick Lane
Ashcombe
Wrenfield
ZZ9 4QT

free office clearances… you cant get better than that.

CARD 2

Peter Radford
Director
peter@kestrelofficeclearance.co.uk
m: 07700 382615

t: 01632 960418

Kestrel Office Clearance
Unit K4 B
2-8 Fenwick Lane
Ashcombe
Wrenfield
ZZ9 4QT

Font styles to use
Sans Serif

Requirements
Must have
• A white background - as we have a blue logo.
Nice to have
• Nice use of the logo - play around with this and dissect it.

```html
<!DOCTYPE html>
<html lang="en">
<head>
<meta charset="utf-8">
<title>Kestrel Office Clearance – Business Card</title>
<link href="https://fonts.googleapis.com/css2?family=Lato:wght@400;700&display=swap" rel="stylesheet">
<style>
  :root {
    --page-bg: #e9e6e1;
    --card-white: #ffffff;
    --card-tint: #eef1f4;
    --brand-blue: #1d5f9f;
    --brand-blue-deep: #134a80;
    --brand-blue-light: #2f80c4;
    --silver: #d6dadf;
    --silver-line: #e4e7ea;
    --name-silver: #c7cbd0;
  }
  html, body {
    margin: 0;
    padding: 0;
    width: 1200px;
    height: 970px;
    overflow: hidden;
    background: var(--page-bg);
    font-family: "Lato", Arial, sans-serif;
  }
  .canvas {
    position: relative;
    width: 1200px;
    height: 970px;
  }
  .business-card {
    position: absolute;
    left: 50px;
    top: 182px;
    width: 1100px;
    height: 606px;
    border-radius: 26px;
    overflow: hidden;
    box-shadow: 0 14px 40px rgba(0,0,0,0.18);
  }
  .business-card svg { display: block; }
  .person-name { font-weight: 700; font-size: 34px; fill: var(--silver); }
  .person-role { font-weight: 400; font-size: 22px; fill: var(--silver); }
  .contact-line { font-weight: 400; font-size: 22px; fill: var(--silver); }
  .address-line { font-weight: 400; font-size: 22px; fill: var(--silver); }
  .company-name { font-weight: 700; font-size: 40px; fill: var(--name-silver); }
  .contact-icon { fill: none; stroke: var(--silver); stroke-width: 2; }
  .contact-icon-solid { fill: var(--silver); }
</style>
</head>
<body>
<main class="canvas">
  <section class="business-card" aria-label="Business card for Mark Holloway, Kestrel Office Clearance">
    <svg width="1100" height="606" viewBox="0 0 1070 590" xmlns="http://www.w3.org/2000/svg">
      <defs>
        <linearGradient id="cardSurface" x1="0" y1="0" x2="1" y2="1">
          <stop offset="0" stop-color="var(--card-white)"/>
          <stop offset="1" stop-color="var(--card-tint)"/>
        </linearGradient>
        <linearGradient id="waveBlue" x1="0" y1="0" x2="1" y2="1">
          <stop offset="0" stop-color="var(--brand-blue-light)"/>
          <stop offset="0.55" stop-color="var(--brand-blue)"/>
          <stop offset="1" stop-color="var(--brand-blue-deep)"/>
        </linearGradient>
      </defs>

      <rect class="card-surface" width="1070" height="590" fill="url(#cardSurface)"/>

      <circle class="brand-circle" cx="248" cy="220" r="152" fill="var(--brand-blue)"/>

      <path class="wave-band" fill="url(#waveBlue)"
            d="M0,340 C80,400 170,435 265,432 C400,428 480,340 600,250 C720,165 850,105 1070,98 L1070,590 L0,590 Z"/>
      <path class="wave-line" fill="none" stroke="var(--silver-line)" stroke-width="3"
            d="M0,395 C100,450 190,482 270,480 C420,472 520,360 640,262 C760,162 880,110 1070,92"/>

      <text class="person-name" x="1010" y="252" text-anchor="end">Mark Holloway</text>
      <text class="person-role" x="1010" y="282" text-anchor="end">Director</text>

      <text class="contact-line" x="975" y="352" text-anchor="end">07700 153928</text>
      <text class="contact-line" x="975" y="385" text-anchor="end">01632 960418</text>
      <text class="contact-line" x="975" y="419" text-anchor="end">mark@kestrelofficeclearance.co.uk</text>
      <text class="contact-line" x="975" y="449" text-anchor="end">www.kestrelofficeclearance.co.uk</text>

      <g class="icon-mobile">
        <rect class="contact-icon" x="993" y="333" width="14" height="22" rx="2"/>
        <line class="contact-icon" x1="996" y1="350" x2="1004" y2="350"/>
      </g>
      <path class="icon-phone contact-icon-solid" transform="translate(989,366) scale(0.85)"
            d="M6.6 10.8c1.4 2.8 3.8 5.1 6.6 6.6l2.2-2.2c.3-.3.7-.4 1-.2 1.1.4 2.3.6 3.6.6.6 0 1 .4 1 1V20c0 .6-.4 1-1 1C10.6 21 3 13.4 3 4c0-.6.4-1 1-1h3.5c.6 0 1 .4 1 1 0 1.3.2 2.5.6 3.6.1.3 0 .7-.2 1z"/>
      <g class="icon-mail">
        <rect class="contact-icon-solid" x="990" y="403" width="20" height="14" rx="1"/>
        <polyline points="990,404 1000,412 1010,404" fill="none" stroke="var(--brand-blue)" stroke-width="1.6"/>
      </g>
      <g class="icon-globe">
        <circle class="contact-icon" cx="1000" cy="442" r="10"/>
        <ellipse class="contact-icon" cx="1000" cy="442" rx="4.5" ry="10"/>
        <line class="contact-icon" x1="990" y1="442" x2="1010" y2="442"/>
        <line class="contact-icon" x1="992" y1="436" x2="1008" y2="436"/>
        <line class="contact-icon" x1="992" y1="448" x2="1008" y2="448"/>
      </g>

      <text class="address-line" x="1010" y="506" text-anchor="end">Unit K4 B, 2-8 Fenwick Lane Ashcombe</text>
      <text class="address-line" x="1010" y="536" text-anchor="end">Wrenfield ZZ9 4QT</text>

      <text class="company-name" x="72" y="534">Kestrel Office Clearance</text>
    </svg>
  </section>
</main>
</body>
</html>
```